Update the A4 Specials Page for Restaurant/Cafe

Provide a MINIMALIST attractive Specials page we can print weekly for our food and drink specials to give to our guests. Final design is to be provided in WORD Document so it can be easily edited by Manager. Should be black text and MINIMALIST to minimise ink usage as we print hundreds a week. We have UPLOADED the existing page as a template for you to update. Maybe logo can stay, see what you think. Or delete it and do something else. Keep it simple. Choose a good FONT. Could be a little playful with a cocktail ICON or something. Our existing menus can be seen at www.saltmeadowcafe.com.au and they are using font Alegreya. Please note we are unable to provide any feedback to designers, however we really do appreciate your time if you are submitting a design. Thank you for your participation.

```html
<!DOCTYPE html>
<html lang="en">
<head>
<meta charset="utf-8">
<title>Salt Meadow Cafe – Weekly Specials</title>
<link href="https://fonts.googleapis.com/css2?family=Alegreya:wght@400;900&display=swap" rel="stylesheet">
<style>
  :root {
    --teal: #355f63;
    --ink: #2f5a5e;
    --paper: #ffffff;
    --backdrop: #e9ebea;
    --pattern: #e4e8ea;
  }
  * { margin: 0; padding: 0; box-sizing: border-box; }
  html, body { width: 1200px; height: 545px; overflow: hidden; background: var(--backdrop); }
  body { font-family: "Alegreya", Georgia, serif; color: var(--ink); }

  .menu-page {
    position: absolute; left: 408px; top: 0;
    width: 384px; height: 545px;
    background: var(--paper);
    overflow: hidden;
  }
  .pattern-area { position: absolute; background: radial-gradient(ellipse at center, var(--pattern) 0%, rgba(228,232,234,0) 70%); }
  .pattern-top { right: -30px; top: -20px; width: 200px; height: 180px; }
  .pattern-bottom { left: -30px; bottom: -30px; width: 220px; height: 170px; }

  .brand {
    position: absolute; left: 0; right: 0; top: 30px;
    display: flex; justify-content: center; align-items: center; gap: 6px;
    padding-left: 72px; width: 310px;
    font-weight: 900; font-size: 17px; color: var(--teal); letter-spacing: 0.3px;
  }
  .brand-dot { width: 9px; height: 9px; border-radius: 50%; background: var(--teal); }

  .page-title {
    position: absolute; left: 77px; top: 78px;
    font-size: 23px; font-weight: 400; color: var(--teal); white-space: nowrap;
  }
  .divider {
    position: absolute; left: 151px; top: 126px; width: 1px; height: 361px; background: var(--teal);
  }

  .section-label {
    position: absolute; left: 26px;
    font-size: 14px; color: var(--teal); white-space: nowrap;
  }
  .section-label::after {
    content: ""; position: absolute; left: -26px; top: 21px; width: 117px; height: 1px; background: var(--teal);
  }
  .label-cocktail { top: 317px; }
  .label-beer { top: 441px; }

  .item { position: absolute; left: 170px; width: 206px; }
  .item-name {
    display: flex; align-items: flex-start; gap: 7px;
    font-weight: 900; font-size: 12px; line-height: 18px; text-transform: uppercase; color: var(--teal);
  }
  .item-name .bullet { flex: none; width: 5px; height: 5px; margin-top: 6px; border-radius: 50%; background: var(--teal); }
  .item-desc { padding-left: 19px; font-size: 9.5px; line-height: 13px; color: var(--ink); }
  .item-price {
    position: absolute; right: 4px;
    font-size: 12px; font-weight: 400; color: var(--ink);
  }
  .item-price sup { font-size: 6.5px; vertical-align: 5px; }

  .item-filo { top: 127px; }
  .item-filo .item-price { top: 54px; }
  .item-soup { top: 228px; }
  .item-soup .item-price { top: 29px; }
  .item-cocktail { top: 339px; }
  .item-cocktail .item-price { top: 44px; }
  .item-beer { top: 463px; }
  .item-beer .item-price { top: 47px; }
</style>
</head>
<body>
  <main class="menu-page">
    <div class="pattern-area pattern-top" role="img" aria-label="Faint scattered leaf pattern"></div>
    <div class="pattern-area pattern-bottom" role="img" aria-label="Faint scattered leaf pattern"></div>

    <div class="brand"><span class="brand-dot"></span>Salt Meadow Cafe</div>
    <h1 class="page-title">Weekly Specials</h1>
    <div class="divider"></div>

    <p class="section-label label-cocktail">Cocktail Special</p>
    <p class="section-label label-beer">Craft Beer Special</p>

    <section class="item item-filo">
      <h2 class="item-name"><span class="bullet"></span>Chicken Filo</h2>
      <p class="item-desc">Creamy Chicken with Pinenuts,<br>wrapped in Filo Pastry.<br>Served with Side Salad &amp; Zulu Sauce</p>
      <p class="item-price"><sup>$</sup>24</p>
    </section>

    <section class="item item-soup">
      <h2 class="item-name"><span class="bullet"></span>Minestrone Soup</h2>
      <p class="item-desc">Served with Garlic Bread</p>
      <p class="item-price"><sup>$</sup>8</p>
    </section>

    <section class="item item-cocktail">
      <h2 class="item-name"><span class="bullet"></span>Passionista</h2>
      <p class="item-desc">Vodka, Passionfruit Pulp, Mango Puree<br>Top up with Ginger &amp; Lemon Kombucha</p>
      <p class="item-price"><sup>$</sup>17</p>
    </section>

    <section class="item item-beer">
      <h2 class="item-name"><span class="bullet"></span>Sly Gecko<br>Sun Burst</h2>
      <p class="item-desc">Tropical Pale Ale 4.8% Alc.</p>
      <p class="item-price"><sup>$</sup>10</p>
    </section>
  </main>
</body>
</html>
```